Letterhead Design Project

Based on the attached logo we would like have a designed of stationary.
As we are a management consulting company focused on business development dealing with C-level and one level below we new business cards.
We have decided to use KMR (Kestrel Meridian Rowe) as the business name. The legal name will be Kestrel Meridian Rowe ApS but we will brand us under KMR. The tack line is “Shaping Lasting Gains” if we need one.
For legal reasons we need to have the legal name on the letters together with the company no. (cvr. nr. 58117904)
We want to signal the following:
- Serious
- Professional
- Creating Result
- Capable of thinking out of the box and creative
- Fast reactions we will be there when needed
What we do not want to be view as is:
- To smart
- We know better
- We can fix it yesterday
Our Value Proposition is two sited:
- Increasing revenue
- Reduced sales cost or increased efficiency
Therefore, companies can call us when they want to grow or they need to be more efficient.
Our business cards should have a two sided print with the logo incl. the tack line on one side and the detailed information on the other site.
We need to have the following information on the letter head:
- Legal company name
- Cvr nr.
- Address incl. country name (Denmark)
- Main number
- Wed address
Symbols are welcome to be used to guide for the above information.
The following information are expected to be in the personal signature of the letter.
- Name
- Title
- Mobile number
- E-mail address
Updates
Some of you has requested our specific details so here they come:
- Address incl. country name (Denmark): Lyngvænget 42, 3460 Birkerød, Denmark
- Main number: +45 7081 5532
- Wed address: www.kmrhalo.com
Mobile no. are +45 xxxx xxxx or +45 2287 3104
Our e-mail looks like this: firstname.seconname@KMRHALO.COM or for me: jonas.vallgren@kmrhalo.com
We need the design (file) as finish as posible so we just need to add personal details before printing.
Please be aware that we will prefer designs where we can print the full letter incl. design. As we are communicating on e-mails with pdf versions of the letter we also need to have a design which will print on the clients printers.
Target Market(s)
C level and one level below.
Major local and international Companies.
Industry/Entity Type
Management Consulting
Font styles to use
Colors
Designer to choose colors to be used in the design.
Requirements
Must have
- Use of our logo without tack line

```html
<!DOCTYPE html>
<html lang="en">
<head>
<meta charset="utf-8">
<title>KMR Business Cards</title>
<link rel="stylesheet" href="https://fonts.googleapis.com/css2?family=Mulish:wght@400;700;800&display=swap">
<style>
  :root {
    --backdrop: #48494b;
    --brand-blue: #1a5fae;
    --brand-blue-deep: #0d4f99;
    --brand-blue-light: #2d8ad0;
    --band-white: #f1f2f2;
    --slate: #575a66;
    --card-white: #f4f4f4;
    --ink: #4a4b50;
    --ink-soft: #5b5c60;
    --rule: #8a8b8e;
  }
  * { box-sizing: border-box; margin: 0; padding: 0; }
  html, body {
    width: 1200px;
    height: 1000px;
    overflow: hidden;
    background: var(--backdrop);
    font-family: "Mulish", sans-serif;
  }
  .card {
    position: absolute;
    width: 530px;
    height: 302px;
    border-radius: 18px;
    overflow: hidden;
  }
  .card-front { left: 137px; top: 149px; }
  .card-front .front-art { position: absolute; inset: 0; display: block; }
  .brand-name {
    position: absolute;
    font-family: "Mulish", sans-serif;
    font-weight: 800;
    line-height: 1;
    letter-spacing: -1px;
  }
  .card-front .brand-name {
    left: 340px;
    top: 50px;
    font-size: 62px;
    color: var(--band-white);
  }
  .card-back {
    left: 491px;
    top: 579px;
    background: var(--card-white);
  }
  .card-back .brand-name {
    left: 39px;
    top: 68px;
    font-size: 60px;
    color: var(--brand-blue);
  }
  .holder {
    position: absolute;
    right: 38px;
    top: 162px;
    text-align: right;
  }
  .holder-name {
    font-weight: 700;
    font-size: 15.5px;
    letter-spacing: 0.6px;
    color: var(--ink);
  }
  .holder-title {
    font-size: 12.5px;
    color: var(--ink-soft);
    margin-top: -1px;
  }
  .divider {
    position: absolute;
    left: 39px;
    right: 38px;
    top: 213px;
    height: 3px;
    border-top: 1px solid var(--rule);
    border-bottom: 1px solid #b9babc;
  }
  .contact {
    position: absolute;
    right: 38px;
    top: 238px;
    text-align: right;
    font-size: 13px;
    line-height: 20px;
    color: var(--ink);
  }
  .contact .label { color: var(--brand-blue); font-weight: 700; }
  .contact .web-name { color: var(--brand-blue); font-weight: 700; }
</style>
</head>
<body>
  <section class="card card-front" aria-label="Business card front">
    <svg class="front-art" width="530" height="302" viewBox="0 0 530 302">
      <defs>
        <linearGradient id="front-blue" x1="0" y1="0" x2="1" y2="1">
          <stop offset="0" stop-color="#2d8ad0"/>
          <stop offset="1" stop-color="#0d4f99"/>
        </linearGradient>
      </defs>
      <rect width="530" height="302" fill="#575a66"/>
      <path d="M0 0 H530 V159 Q290 250 0 136 Z" fill="url(#front-blue)"/>
      <path d="M0 136 Q290 250 530 159 V176 Q290 272 0 191 Z" fill="#f1f2f2"/>
    </svg>
    <div class="brand-name">KMR</div>
  </section>

  <section class="card card-back" aria-label="Business card back">
    <div class="brand-name">KMR</div>
    <div class="holder">
      <div class="holder-name">MARA LINDQVIST</div>
      <div class="holder-title">Manager</div>
    </div>
    <div class="divider"></div>
    <div class="contact">
      <div>Lyngvænget 42, 7190, Billund, Jutland · <span class="label">T:</span> +45 2287 3104</div>
      <div><span class="label">E:</span> info@kmrhalo.com · www.<span class="web-name">kmrhalo</span>.com</div>
    </div>
  </section>
</body>
</html>
```